Business Card Design - Amberfield Court

We are looking at a new design for our business cards that has a modern and professional look. We run a residential aged care facility focussing on the care of residents. The cards will be used for potential clients, consultants and business opportunities in this sector. Blue and white is our main colours and would to see these colours incorporated in the design.
Industry/Entity Type
Business
Contact Information for Business Card
Amberfield Court, Darren Walsh, dwalsh@amberfieldcourt.com.au, Finance Manager, 0472 639 208, BCom, 37 Marrabel Crescent, Brindle Vale, Qld 4093.
Look and feel
Each slider illustrates characteristics of the customer's brand and the style your logo design should communicate.

```html
<!DOCTYPE html>
<html lang="en">
<head>
<meta charset="utf-8">
<title>Amberfield Court – Business Card</title>
<link rel="stylesheet" href="https://fonts.googleapis.com/css2?family=Arimo:wght@400;700&display=swap">
<style>
  :root {
    --brand-blue: #4b7f9b;
    --brand-blue-light: #6d9bb4;
    --card-white: #ffffff;
    --card-grey: #e9ecee;
    --text-dark: #2f3a40;
    --text-grey: #5c6367;
    --page-bg: #d9dcde;
  }
  * { box-sizing: border-box; margin: 0; padding: 0; }
  html, body {
    width: 1200px; height: 950px; overflow: hidden;
    background: var(--page-bg);
    font-family: "Arimo", Arial, sans-serif;
  }
  .sheet {
    width: 1200px; height: 950px;
    display: flex; flex-direction: column;
    align-items: center; justify-content: center; gap: 40px;
  }
  .card {
    position: relative;
    width: 680px; height: 416px;
    background: var(--card-white);
    box-shadow: 0 6px 18px rgba(0,0,0,.18);
    overflow: hidden;
  }

  /* Back */
  .card-back {
    background: linear-gradient(120deg, #ffffff 0%, var(--card-grey) 100%);
    display: flex; align-items: center; justify-content: center;
  }
  .back-name {
    font-size: 44px; font-weight: 700; letter-spacing: 2px;
    text-transform: uppercase; color: var(--brand-blue);
  }

  /* Front */
  .front-band {
    position: absolute; left: 0; top: 0;
    width: 100%; height: 200px;
    background: var(--brand-blue);
  }
  .holder {
    position: absolute; left: 40px; top: 32px; color: var(--card-white);
  }
  .holder-name {
    font-size: 26px; font-weight: 700; letter-spacing: 1px; text-transform: uppercase;
  }
  .holder-name .credential { font-size: 19px; }
  .holder-role {
    margin-top: 10px; font-size: 15px; letter-spacing: 1px;
    text-transform: uppercase; color: #dbe7ee;
  }
  .illustration {
    position: absolute; left: 420px; top: 90px;
    width: 230px; height: 210px;
    background: linear-gradient(180deg, #f4f7f9 0%, #ffffff 100%);
    border-radius: 90px 90px 0 0;
  }
  .contact-list {
    position: absolute; left: 40px; top: 232px;
    list-style: none; color: var(--text-dark); font-size: 19px;
  }
  .contact-list li { display: flex; align-items: center; gap: 10px; line-height: 30px; }
  .contact-icon { width: 18px; height: 18px; flex: none; }
  .address {
    position: absolute; right: 40px; bottom: 34px;
    text-align: right; color: var(--text-grey); font-size: 20px; line-height: 28px;
  }
</style>
</head>
<body>
<main class="sheet">

  <section class="card card-back" aria-label="Card back">
    <span class="back-name">Amberfield Court</span>
  </section>

  <section class="card card-front" aria-label="Card front">
    <div class="front-band"></div>
    <div class="holder">
      <p class="holder-name">Darren Walsh <span class="credential">BCom</span></p>
      <p class="holder-role">Finance Manager</p>
    </div>
    <div class="illustration" role="img" aria-label="Silhouette illustration of a carer walking with a resident"></div>

    <ul class="contact-list">
      <li>
        <svg class="contact-icon" viewBox="0 0 18 18" aria-hidden="true">
          <circle cx="9" cy="9" r="9" fill="var(--brand-blue)"/>
          <path d="M5.5 4.5h2l1 2.5-1.3 1a6 6 0 0 0 2.8 2.8l1-1.3 2.5 1v2a1 1 0 0 1-1 1A8 8 0 0 1 4.5 5.5a1 1 0 0 1 1-1z" fill="#fff"/>
        </svg>
        0472 639 208
      </li>
      <li>
        <svg class="contact-icon" viewBox="0 0 18 18" aria-hidden="true">
          <rect x="1" y="4" width="16" height="10" rx="1" fill="var(--brand-blue)"/>
          <path d="M1.5 4.5 9 10l7.5-5.5" fill="none" stroke="#fff" stroke-width="1.3"/>
        </svg>
        dwalsh@amberfieldcourt.com.au
      </li>
      <li>
        <svg class="contact-icon" viewBox="0 0 18 18" aria-hidden="true">
          <circle cx="9" cy="9" r="9" fill="var(--brand-blue)"/>
          <circle cx="9" cy="9" r="5.5" fill="none" stroke="#fff" stroke-width="1.2"/>
          <path d="M3.5 9h11M9 3.5c-2.5 3-2.5 8 0 11M9 3.5c2.5 3 2.5 8 0 11" fill="none" stroke="#fff" stroke-width="1"/>
        </svg>
        www.amberfieldcourt.com.au
      </li>
    </ul>

    <address class="address" style="font-style:normal">
      37 Marrabel Crescent<br>
      Brindle Vale, Qld 4093.
    </address>
  </section>

</main>
</body>
</html>
```